Copper lark buildworks

Copper lark buildworks is a small construction company.
Who is a licenced builder, Carpenter, joiner,
working on heritage ,new build, speacial projects and sometimes furniture

Industry/Entity Type

Construction

```html
<!DOCTYPE html>
<html lang="en">
<head>
<meta charset="utf-8">
<title>Copper lark buildworks – Business Card</title>
<link rel="stylesheet" href="https://fonts.googleapis.com/css2?family=Open+Sans:wght@400;600&display=swap">
<style>
  :root {
    --page-bg: #e8e4de;
    --navy: #0e5479;
    --sky: #29a3e0;
    --paper: #ffffff;
    --ink: #4a4a4a;
    --title-ink: #d6e6f0;
  }
  * { margin: 0; padding: 0; box-sizing: border-box; }
  html, body {
    width: 1200px;
    height: 828px;
    overflow: hidden;
    background: var(--page-bg);
    font-family: "Open Sans", sans-serif;
  }
  .business-card {
    position: absolute;
    left: 100px;
    top: 131px;
    width: 1000px;
    height: 566px;
    background: var(--paper);
    overflow: hidden;
    box-shadow: 0 6px 22px rgba(0,0,0,0.18);
  }
  .card-shapes {
    position: absolute;
    inset: 0;
    width: 1000px;
    height: 566px;
  }
  .brand-name {
    position: absolute;
    left: 133px;
    top: 188px;
    width: 300px;
    text-align: center;
    color: var(--sky);
    font-weight: 600;
    font-size: 23px;
    line-height: 1.1;
  }
  .person {
    position: absolute;
    right: 56px;
    top: 150px;
    text-align: right;
  }
  .person-name {
    color: var(--sky);
    font-size: 27px;
    font-weight: 400;
    letter-spacing: 1px;
    line-height: 1.2;
  }
  .person-title {
    color: var(--title-ink);
    font-size: 17px;
    letter-spacing: 4px;
    line-height: 1.3;
  }
  .contact-list {
    position: absolute;
    top: 366px;
    list-style: none;
    color: var(--ink);
    font-size: 25px;
  }
  .contact-list li {
    display: flex;
    align-items: center;
    height: 35px;
  }
  .contact-list svg { width: 22px; height: 22px; fill: var(--sky); flex: none; }
  .contact-phones { left: 36px; }
  .contact-phones svg { margin-right: 24px; }
  .contact-online { right: 52px; }
  .contact-online li { justify-content: flex-end; }
  .contact-online svg { margin-left: 20px; }
</style>
</head>
<body>
  <div class="business-card">
    <svg class="card-shapes" viewBox="0 0 1000 566" aria-hidden="true">
      <rect class="header-band" x="0" y="0" width="1000" height="244" fill="var(--navy)"/>
      <polygon class="roof-shape" points="283,37 521,244 52,244" fill="var(--paper)"/>
      <rect class="footer-band" x="0" y="492" width="1000" height="74" fill="var(--sky)"/>
      <polygon class="footer-accent" points="60,492 506,492 564,566 0,566" fill="var(--navy)"/>
    </svg>

    <div class="brand-name">Copper lark buildworks</div>

    <div class="person">
      <div class="person-name">PERSONS NAME</div>
      <div class="person-title">PERSONS TITLE</div>
    </div>

    <ul class="contact-list contact-phones">
      <li>
        <svg viewBox="0 0 24 24"><path d="M6.6 10.8a15.2 15.2 0 0 0 6.6 6.6l2.2-2.2c.3-.3.7-.4 1-.2 1.1.4 2.3.6 3.6.6.6 0 1 .4 1 1V20c0 .6-.4 1-1 1C10.6 21 3 13.4 3 4c0-.6.4-1 1-1h3.5c.6 0 1 .4 1 1 0 1.3.2 2.5.6 3.6.1.3 0 .7-.2 1z"/></svg>
        (999) 222-5555
      </li>
      <li>
        <svg viewBox="0 0 24 24"><path d="M8 2h8a2 2 0 0 1 2 2v16a2 2 0 0 1-2 2H8a2 2 0 0 1-2-2V4a2 2 0 0 1 2-2zm0 3v12h8V5zm4 13.5a1 1 0 1 0 0 2 1 1 0 0 0 0-2z"/></svg>
        (999) 222-4444
      </li>
      <li>
        <svg viewBox="0 0 24 24"><path d="M7 3h10v4H7zM4 8h16a2 2 0 0 1 2 2v6h-4v5H6v-5H2v-6a2 2 0 0 1 2-2zm4 7v4h8v-4z"/></svg>
        (999) 222-3333
      </li>
    </ul>

    <ul class="contact-list contact-online">
      <li>
        aaaaaa@nnn.com
        <svg viewBox="0 0 24 24"><path d="M2 5h20v14H2zm2 2v.5l8 5 8-5V7zm0 2.8V17h16V9.8l-8 5z"/></svg>
      </li>
      <li>
        www.sssssss.com
        <svg viewBox="0 0 24 24"><path d="M12 2a10 10 0 1 0 0 20 10 10 0 0 0 0-20zm6.9 9h-3a15 15 0 0 0-1.4-6A8 8 0 0 1 18.9 11zM12 4.1c.9 1.3 1.7 3.6 1.9 6.9h-3.8c.2-3.3 1-5.6 1.9-6.9zM9.5 5a15 15 0 0 0-1.4 6h-3A8 8 0 0 1 9.5 5zm-4.4 8h3a15 15 0 0 0 1.4 6 8 8 0 0 1-4.4-6zm6.9 6.9c-.9-1.3-1.7-3.6-1.9-6.9h3.8c-.2 3.3-1 5.6-1.9 6.9zm2.5-.9a15 15 0 0 0 1.4-6h3a8 8 0 0 1-4.4 6z"/></svg>
      </li>
      <li>
        City, State Name, 77 Street Name str.
        <svg viewBox="0 0 24 24"><path d="M12 2a7 7 0 0 0-7 7c0 5.2 7 13 7 13s7-7.8 7-13a7 7 0 0 0-7-7zm0 9.5a2.5 2.5 0 1 1 0-5 2.5 2.5 0 0 1 0 5z"/></svg>
      </li>
    </ul>
  </div>
</body>
</html>
```